Kelvaro Stationary
Cards, letterhead, envelopes
Simple
Tomas Pelling
General Manager
4827 Harrowfield Lane, Suite 100
Oceanside CA, 92071
Use place holder
Use Place Holder
tpelling@kelvaroglassworks.com
www.kelvaroglassworks.com
Play with a 1 sided vs 2 sided options for business cards. I am open to both. Need stationary as well.
Use this logo
.ai version

```html
<!DOCTYPE html>
<html lang="en">
<head>
<meta charset="utf-8">
<title>Kelvaro Stationary</title>
<link href="https://fonts.googleapis.com/css2?family=Questrial&display=swap" rel="stylesheet">
<style>
  :root {
    --backdrop: #d9d5cf;
    --paper: #ffffff;
    --paper-edge: #e6e4e1;
    --ink: #3b3b3b;
    --ink-soft: #6d6d6d;
    --accent: #c8701e;
    --card-dark: #4a4a4a;
    --card-dark-edge: #5d5d5d;
    --ghost: #ecebea;
  }
  * { box-sizing: border-box; margin: 0; padding: 0; }
  html, body { width: 1200px; height: 866px; overflow: hidden; }
  body {
    background: var(--backdrop);
    font-family: "Questrial", "Century Gothic", sans-serif;
    color: var(--ink);
    position: relative;
  }
  .piece {
    position: absolute;
    background: var(--paper);
    overflow: hidden;
    box-shadow: 0 2px 6px rgba(0,0,0,.25);
  }
  .wordmark {
    display: flex; align-items: center; gap: 6px;
    color: var(--ink); font-size: 30px; line-height: 1; letter-spacing: -.5px;
  }
  .wordmark .dot {
    width: 22px; height: 22px; border-radius: 50%; background: var(--accent);
  }
  .divider { position: absolute; width: 1px; background: #bdbdbd; }
  .details { position: absolute; font-size: 9px; line-height: 1.45; color: var(--ink-soft); }
  .ghost-mark { position: absolute; border-radius: 50%; border: 18px solid var(--ghost); }

  /* Letterhead */
  .letterhead { left: 48px; top: 43px; width: 499px; height: 720px; }
  .letterhead .wordmark { position: absolute; left: 38px; top: 56px; }
  .letterhead .divider { left: 228px; top: 52px; height: 95px; }
  .letterhead .details { left: 240px; top: 54px; }
  .letterhead .ghost-mark { left: 232px; top: 478px; width: 250px; height: 250px; }

  /* Envelopes */
  .envelope-back { left: 497px; top: 245px; width: 607px; height: 247px; }
  .envelope-back svg { position: absolute; inset: 0; }
  .envelope-back .seal { position: absolute; left: 277px; top: 28px; width: 50px; height: 50px; border-radius: 50%; border: 6px solid var(--ghost); }
  .envelope-front { left: 569px; top: 360px; width: 590px; height: 269px; }
  .envelope-front .wordmark { position: absolute; left: 20px; top: 42px; }
  .envelope-front .divider { left: 184px; top: 36px; height: 86px; }
  .envelope-front .details { left: 196px; top: 38px; }
  .envelope-front .ghost-mark { left: 430px; top: 122px; width: 170px; height: 170px; border-width: 14px; }

  /* Business cards */
  .card { border-radius: 8px; }
  .card-front .wordmark { position: absolute; font-size: 24px; }
  .card-front .wordmark .dot { width: 17px; height: 17px; }
  .card-front .person { position: absolute; font-size: 10px; line-height: 1.3; }
  .card-front .person .role { color: var(--ink-soft); font-size: 7.5px; }
  .card-front .person .email { color: var(--ink-soft); font-size: 7px; margin-top: 6px; }
  .card-front .details { font-size: 6.5px; }

  .card-one { left: 595px; top: 84px; width: 178px; height: 103px; }
  .card-one .wordmark { left: 12px; top: 14px; }
  .card-one .person { left: 12px; top: 55px; }
  .card-one .divider { left: 100px; top: 52px; height: 40px; }
  .card-one .details { left: 106px; top: 52px; }

  .card-dark { left: 792px; top: 84px; width: 180px; height: 103px;
    background: linear-gradient(135deg, var(--card-dark-edge), var(--card-dark)); }
  .card-dark .mark { position: absolute; left: 70px; top: 30px; width: 40px; height: 40px; border-radius: 50%; border: 4px solid #6b6b6b; }
  .card-dark .web { position: absolute; left: 0; right: 0; top: 80px; text-align: center; font-size: 5.5px; color: #9a9a9a; }

  .card-two { left: 629px; top: 653px; width: 206px; height: 120px; }
  .card-two .wordmark { left: 22px; top: 16px; }
  .card-two .person { left: 16px; top: 64px; }
  .card-two .divider { left: 114px; top: 60px; height: 46px; }
  .card-two .details { left: 120px; top: 60px; }

  .card-light { left: 859px; top: 653px; width: 178px; height: 120px; }
  .card-light .mark { position: absolute; left: 64px; top: 22px; width: 50px; height: 50px; border-radius: 50%; background: var(--accent); }
  .card-light .web { position: absolute; left: 0; right: 0; top: 92px; text-align: center; font-size: 6px; color: var(--ink-soft); }
</style>
</head>
<body>

  <section class="piece letterhead" aria-label="Letterhead">
    <div class="wordmark"><span class="dot"></span>kelvaro</div>
    <div class="divider"></div>
    <div class="details">
      4827 Harrowfield Lane, Suite 100<br>
      Oceanside CA, 92071<br><br>
      Toll Free: 000-000-0000<br>
      Cell: 000-000-0000<br>
      Phone: 000-000-0000<br>
      Fax: 000-000-0000
    </div>
    <div class="ghost-mark"></div>
  </section>

  <section class="piece envelope-back" aria-label="Envelope back">
    <svg width="607" height="247" viewBox="0 0 607 247">
      <path d="M0 2 L290 84 Q303 88 316 84 L607 2" fill="none" stroke="#dcdcdc" stroke-width="1.5"/>
    </svg>
    <div class="seal"></div>
  </section>

  <section class="piece envelope-front" aria-label="Envelope front">
    <div class="wordmark"><span class="dot"></span>kelvaro</div>
    <div class="divider"></div>
    <div class="details">
      4827 Harrowfield Lane, Suite 100<br>
      Oceanside CA, 92071<br>
      Toll Free: 000-000-0000<br>
      Cell: 000-000-0000<br>
      Phone: 000-000-0000<br>
      Fax: 000-000-0000
    </div>
    <div class="ghost-mark"></div>
  </section>

  <section class="piece card card-front card-one" aria-label="Business card front">
    <div class="wordmark"><span class="dot"></span>kelvaro</div>
    <div class="person">Tomas Pelling<div class="role">General Manager</div></div>
    <div class="divider"></div>
    <div class="details">
      4827 Harrowfield Lane<br>
      Oceanside CA, 92071<br>
      Cell: 000-000-0000<br>
      Phone: 000-000-0000<br>
      Fax: 000-000-0000
    </div>
  </section>

  <section class="piece card card-dark" aria-label="Business card back, dark">
    <div class="mark"></div>
    <div class="web">www.kelvaroglassworks.com</div>
  </section>

  <section class="piece card card-front card-two" aria-label="Business card front">
    <div class="wordmark"><span class="dot"></span>kelvaro</div>
    <div class="person">Tomas Pelling<div class="role">General Manager</div>
      <div class="email">tpelling@kelvaroglassworks.com</div></div>
    <div class="divider"></div>
    <div class="details">
      4827 Harrowfield Lane<br>
      Oceanside CA, 92071<br>
      Cell: 000-000-0000<br>
      Phone: 000-000-0000<br>
      Fax: 000-000-0000
    </div>
  </section>

  <section class="piece card card-light" aria-label="Business card back, light">
    <div class="mark"></div>
    <div class="web">www.kelvaroglassworks.com</div>
  </section>

</body>
</html>
```